MRT Property - Business Cards

Looking for a business card & general letterhead, signage etc design for our new logo.

Colours:
000a20
0056a2
00b5ef
0088ce
68cef2

Fonts:
Poppins
Karla

Please keep look and feel of new brand - example in the zip package I sent.

```html
<!DOCTYPE html>
<html lang="en">
<head>
<meta charset="utf-8">
<title>MRT Property – Business Cards</title>
<link href="https://fonts.googleapis.com/css2?family=Poppins:wght@600&family=Montserrat:wght@500&family=Itim&display=swap" rel="stylesheet">
<style>
  :root {
    --navy: #000a20;
    --brand-blue: #0056a2;
    --sky: #00b5ef;
    --mid-blue: #0088ce;
    --pale-blue: #68cef2;
    --band-2: #1fb1e8;
    --band-3: #1a88cb;
    --band-4: #0b55a3;
    --card: #ffffff;
    --ink: #1a1a1a;
    --backdrop: #e9e6e1;
  }
  * { margin: 0; padding: 0; box-sizing: border-box; }
  html, body { width: 900px; height: 1200px; overflow: hidden; }
  body { background: var(--backdrop); position: relative; font-family: "Montserrat", sans-serif; }

  .card {
    position: absolute;
    left: 80px;
    width: 742px;
    height: 440px;
    background: var(--card);
    border-radius: 24px;
    overflow: hidden;
    box-shadow: 0 6px 18px rgba(0, 0, 0, 0.18);
  }
  .card--front { top: 131px; }
  .card--back { top: 638px; }

  .card__band {
    position: absolute;
    left: 0; right: 0; bottom: 0;
    height: 18px;
    display: flex;
  }
  .card__band span { flex: 1; }
  .card__band span:nth-child(1) { background: var(--pale-blue); }
  .card__band span:nth-child(2) { background: var(--band-2); }
  .card__band span:nth-child(3) { background: var(--band-3); }
  .card__band span:nth-child(4) { background: var(--band-4); }

  .wordmark {
    position: absolute;
    font-family: "Poppins", sans-serif;
    font-weight: 600;
    color: var(--brand-blue);
    white-space: nowrap;
    line-height: 1;
  }
  .card--front .wordmark { left: 64px; top: 200px; font-size: 34px; }
  .card--back .wordmark { left: 0; right: 0; top: 176px; text-align: center; font-size: 66px; }

  .contact {
    position: absolute;
    left: 355px;
    top: 109px;
    height: 224px;
    border-left: 2px solid var(--brand-blue);
    padding-left: 15px;
    color: var(--ink);
  }
  .contact__name {
    font-family: "Itim", cursive;
    font-size: 31px;
    color: var(--brand-blue);
    line-height: 1;
    margin-top: 1px;
  }
  .contact__role { font-size: 15px; margin-top: 6px; }
  .contact__address { font-size: 15px; line-height: 21px; margin-top: 22px; }
  .contact__list { list-style: none; margin-top: 21px; font-size: 15px; }
  .contact__list li { display: flex; align-items: center; height: 28px; }
  .contact__list svg { width: 15px; height: 15px; margin-right: 12px; fill: var(--brand-blue); flex: none; }
</style>
</head>
<body>

<section class="card card--front">
  <div class="wordmark">MRT Property</div>

  <div class="contact">
    <p class="contact__name">Daniel Reyes</p>
    <p class="contact__role">Managing Director</p>
    <p class="contact__address">420 Maple Ridge Ave Suite<br>210 Dayton Ohio 45402</p>
    <ul class="contact__list">
      <li>
        <svg viewBox="0 0 24 24" aria-hidden="true"><path d="M6.6 10.8a15.1 15.1 0 0 0 6.6 6.6l2.2-2.2c.3-.3.7-.4 1-.2 1.1.4 2.3.6 3.6.6.6 0 1 .4 1 1V20c0 .6-.4 1-1 1A17 17 0 0 1 3 4c0-.6.4-1 1-1h3.5c.6 0 1 .4 1 1 0 1.3.2 2.5.6 3.6.1.3 0 .7-.2 1z"/></svg>
        1 (555) 014-2736
      </li>
      <li>
        <svg viewBox="0 0 24 24" aria-hidden="true"><path d="M2 5h20v14H2z M2 5l10 7 10-7" fill="none" stroke="currentColor"/><path d="M2 6v13h20V6l-10 7z"/><path d="M2 5h20l-10 7z"/></svg>
        info@mrtproperty.com
      </li>
      <li>
        <svg viewBox="0 0 24 24" aria-hidden="true"><path d="M12 2a10 10 0 1 0 0 20 10 10 0 0 0 0-20zm-1 17.9A8 8 0 0 1 4.2 10L9 14.8v1a2 2 0 0 0 2 2zm6.9-2.5a2 2 0 0 0-1.9-1.4h-1v-3a1 1 0 0 0-1-1H8v-2h2a1 1 0 0 0 1-1V7h2a2 2 0 0 0 2-2v-.4a8 8 0 0 1 2.9 12.8z"/></svg>
        www.mrtproperty.com
      </li>
    </ul>
  </div>

  <div class="card__band"><span></span><span></span><span></span><span></span></div>
</section>

<section class="card card--back">
  <div class="wordmark">MRT Property</div>
  <div class="card__band"><span></span><span></span><span></span><span></span></div>
</section>

</body>
</html>
```